Design a modern, classy & professional business card for an online real estate agency, specializing in medium-luxury properties in Thailand and later in Singapore and UK.

Possible design ideas so far: (not essential)

- curved corner(s) to the card, white on front & turquoise on back or visa versa.

- front of card - clear and simple, company name in metallic grey/monochrome, logo graphic & company name on front in spot UV or embossed/debossed effect.

- back of card - large, close-cropped, 'ghost' patterns of the C-shaped curves of logo, or company name repeated on back of card in spot UV.

Target Market(s)

- young to middle-aged professionals mainly (but ideally should design should suit all)

- UK, US,EU,AUS & ASIAN mainly (but ideally should design should suit all countries)

Industry/Entity Type

Real Estate

Requirements
Must have
• THEME:
- Luxurious & Modern
- Clean & striking
- Unique & creative

INFO:
- Logo & company name on front
- Contact details on back:

Tobias Hennlund
Managing Director

www.velmontestates.asia
www.velmontestates.co.uk

Tel: 083-274-6159
email: tobias@velmontestates.asia

(contact details can be displayed in any order as suites design.)

Nice to have
• - curved corner(s) to the card, white on front & turquoise on back or visa versa.

Should not have
• - No generic images of properties, palm trees/coconut trees etc.

- No other other bold colors, except for main turquoise, grey, metallic white & black theme.

- No obvious business card templates

```html
<!DOCTYPE html>
<html lang="en">
<head>
<meta charset="utf-8">
<title>Velmont Estates – Business Card</title>
<link rel="stylesheet" href="https://fonts.googleapis.com/css2?family=Libre+Baskerville&family=Open+Sans:wght@400;600&display=swap">
<style>
  :root {
    --page-bg: #ececec;
    --turquoise: #4fc4c0;
    --turquoise-deep: #3aaeaa;
    --turquoise-light: #8fe3df;
    --grey-text: #7d7f82;
    --ink: #3e4246;
    --card-white: #ffffff;
    --brand-font: "Libre Baskerville", Georgia, serif;
    --body-font: "Open Sans", Arial, sans-serif;
  }
  * { box-sizing: border-box; margin: 0; padding: 0; }
  html, body {
    width: 900px; height: 1200px; overflow: hidden;
    background: var(--page-bg);
  }
  .canvas {
    position: relative; width: 900px; height: 1200px;
    display: flex; flex-direction: column; align-items: center;
  }

  /* Brand lockup */
  .lockup { display: flex; align-items: center; gap: 14px; }
  .lockup-square { background: var(--turquoise); flex: none; }
  .lockup-name {
    font-family: var(--brand-font); color: var(--grey-text);
    font-weight: 400; line-height: 1;
  }
  .lockup-name .word-main { display: block; }
  .lockup-name .word-sub { display: block; letter-spacing: 0.2em; }

  .page-lockup { margin-top: 48px; }
  .page-lockup .lockup-square { width: 82px; height: 82px; }
  .page-lockup .word-main { font-size: 46px; }
  .page-lockup .word-sub { font-size: 19px; margin-top: 8px; }

  /* Cards */
  .card {
    width: 540px; height: 424px; border-radius: 34px; overflow: hidden;
    position: relative;
  }
  .card-back { margin-top: 42px; }
  .card-front { margin-top: 40px; background: var(--card-white); }

  .back-pattern { position: absolute; inset: 0; display: block; }
  .back-name {
    position: absolute; inset: 0;
    display: flex; align-items: center; justify-content: center;
    font-family: var(--brand-font); font-size: 40px; color: #ffffff;
  }

  .card-front .lockup { position: absolute; left: 50px; top: 52px; }
  .card-front .lockup-square { width: 62px; height: 62px; }
  .card-front .word-main { font-size: 36px; }
  .card-front .word-sub { font-size: 14px; margin-top: 6px; }

  .contact {
    position: absolute; left: 50px; top: 190px;
    font-family: var(--body-font); color: var(--ink);
  }
  .contact-name { font-size: 17px; font-weight: 600; }
  .contact-role { font-size: 13px; margin-top: 3px; }
  .contact-lines { margin-top: 24px; font-size: 13px; line-height: 1.6; }
  .contact-web { margin-top: 18px; font-size: 13px; line-height: 1.6; }
</style>
</head>
<body>
<main class="canvas">

  <header class="lockup page-lockup">
    <span class="lockup-square"></span>
    <span class="lockup-name">
      <span class="word-main">Velmont</span>
      <span class="word-sub">ESTATES</span>
    </span>
  </header>

  <section class="card card-back">
    <svg class="back-pattern" viewBox="0 0 540 424" preserveAspectRatio="none" role="img" aria-label="Spot UV ghost pattern of interlocking curved shapes on turquoise">
      <defs>
        <linearGradient id="backTone" x1="0" y1="0" x2="1" y2="1">
          <stop offset="0" stop-color="#4fc4c0"/>
          <stop offset="0.55" stop-color="#3aaeaa"/>
          <stop offset="1" stop-color="#6fd6d2"/>
        </linearGradient>
      </defs>
      <rect width="540" height="424" fill="url(#backTone)"/>
    </svg>
    <div class="back-name">Velmont Estates</div>
  </section>

  <section class="card card-front">
    <div class="lockup">
      <span class="lockup-square"></span>
      <span class="lockup-name">
        <span class="word-main">Velmont</span>
        <span class="word-sub">ESTATES</span>
      </span>
    </div>
    <div class="contact">
      <p class="contact-name">Tobias Hennlund</p>
      <p class="contact-role">Managing Director</p>
      <div class="contact-lines">
        <p>083-274-6159</p>
        <p>tobias@velmontestates.asia</p>
      </div>
      <div class="contact-web">
        <p>www.velmontestates.asia</p>
        <p>www.velmontestates.co.uk</p>
      </div>
    </div>
  </section>

</main>
</body>
</html>
```